Catering Menu Package

I currently have a complete menu package, which we have redesigned as far as content, now I need to it put together in a catalog type format. It is essentially 10-12 pages in length, and will be sent for print production. Upon receiving a final edit
Updates

I have added an example gif to the project.

I did this free hand this basically what I am looking for. please change text and type to whatever you think would look best. This is a total rough design so, feel free to change any and everything. The text for the page is on the word documents. If you need more images let me know I am in the process of getting as many images uploaded for your use.

Project Deadline Extended
Reason: I figured we got a late jump with questions, so i am extending a few days .

Target Market(s)

The target market is business who wish to have catered luncheons, breakfasts , meetings

Industry/Entity Type

Catering

Requirements
Must have
• I have attached a copy of the text that what we want in the package, our logo, and i have also attached a catering package of another company to give you an idea what the finished product will be
Should not have
• It should not look identical to the example catering packages, these are for some inspiration we want our own design with the same type of look and feel

```html
<!DOCTYPE html>
<html lang="en">
<head>
<meta charset="utf-8">
<title>Hearty Breakfast – Harvest Table Caterers</title>
<link rel="stylesheet" href="https://fonts.googleapis.com/css2?family=Noto+Serif:ital,wght@0,400;0,700;1,400;1,700&family=Pinyon+Script&display=swap">
<style>
  :root {
    --page: #fbf9f7;
    --strip-top: #f4efec;
    --strip-bottom: #dcd0c8;
    --ink: #6a5a52;
    --heading-brown: #7b3815;
    --heading-maroon: #8c1a3e;
    --title: #5e4a40;
    --logo: #2b2320;
    --accent: #e0782c;
  }
  html, body { margin: 0; padding: 0; overflow: hidden; }
  body { width: 1200px; height: 927px; background: var(--page); }
  .menu-page {
    position: relative; width: 1200px; height: 927px; overflow: hidden;
    background: radial-gradient(ellipse at 70% 30%, #ffffff 0%, var(--page) 60%, #f1ece8 100%);
    font-family: "Noto Serif", Georgia, serif; color: var(--ink);
  }
  .side-strip {
    position: absolute; left: 0; top: 0; width: 183px; height: 927px;
    background: linear-gradient(180deg, var(--strip-top) 0%, #ece4df 55%, var(--strip-bottom) 100%);
  }
  .brand {
    position: absolute; left: 28px; top: 40px; width: 130px;
    font-family: "Noto Serif", Georgia, serif; font-weight: 700; font-size: 21px;
    line-height: 1.2; color: var(--logo); text-transform: lowercase;
  }
  .brand-mark { display: block; width: 34px; height: 34px; background: var(--accent); margin-bottom: 14px; }
  .page-title {
    position: absolute; left: 196px; top: 44px; margin: 0;
    font-family: "Pinyon Script", cursive; font-weight: 400; font-size: 48px; color: var(--title);
  }
  .menu-item { position: absolute; margin: 0; font-size: 17px; line-height: 24px; }
  .menu-item h2 {
    margin: 0; font-style: italic; font-weight: 700; font-size: 18px; line-height: 24px;
  }
  .menu-item h2.big { font-size: 20px; }
  .col-left h2 { color: var(--heading-brown); }
  .col-right h2 { color: var(--heading-maroon); font-weight: 400; }
  .menu-item p { margin: 0; }
  .menu-item em.lead { font-style: italic; font-weight: 700; }
  .col-left { left: 196px; width: 470px; }
  .col-right { left: 689px; width: 470px; }
  .price-note { font-style: italic; }
  .price-note .price { margin-left: 18px; }
  .photo-band { position: absolute; top: 700px; height: 227px; }
  .photo-plate {
    left: 183px; width: 470px;
    background: radial-gradient(ellipse at 40% 70%, #f6f1e6 0%, #e9c89a 35%, #b5652e 65%, #7c3a1c 100%);
    border-top-left-radius: 60px; border-top-right-radius: 120px;
  }
  .photo-wraps {
    left: 655px; width: 260px;
    background: linear-gradient(160deg, #ead7b6 0%, #d9b88b 45%, #c8a272 100%);
    border-top-left-radius: 40px; border-top-right-radius: 40px;
  }
  .photo-quiche {
    left: 880px; top: 712px; width: 340px; height: 240px; border-radius: 50%;
    background: radial-gradient(circle at 50% 45%, #d8b94e 0%, #c2a447 35%, #eae7e2 62%, #ffffff 80%);
  }
</style>
</head>
<body>
<main class="menu-page">
  <aside class="side-strip">
    <div class="brand"><span class="brand-mark"></span>harvest table caterers</div>
  </aside>

  <h1 class="page-title">Hearty Breakfast</h1>

  <section class="menu-item col-left" style="top:140px;">
    <h2>Breakfast Croissantwich</h2>
    <p>Farm-fresh Eggs &amp; Cheese, Farm-fresh Eggs &amp; Applewood Smoked Bacon, Farm-Fresh Eggs &amp; Maple Sausage, or Farm-Fresh Eggs &amp; Scrapple.</p>
  </section>

  <section class="menu-item col-left" style="top:260px;">
    <p><em class="lead">Don’t want a Croissant?</em> Sandwich size English Muffins, Fresh Baked Biscuits, &amp; Brooklyn Bagels available on request.</p>
  </section>

  <section class="menu-item col-left" style="top:350px;">
    <h2 class="big">Chef Mateo’s Breakfast Burrito</h2>
    <p>Jumbo flour tortilla filled with Redskin Potatoes, Farm-fresh Eggs, Shredded Cheddar, &amp; your choice of meat or extra cheese.</p>
  </section>

  <section class="menu-item col-left" style="top:470px;">
    <p><em class="lead">Choose from:</em> Chorizo Sausage, Applewood Smoked Bacon, Maple Sausage, or Country Ham. Served with fresh Chef made Salsa.</p>
  </section>

  <section class="menu-item col-left" style="top:568px;">
    <p class="price-note">Add avocado <span class="price">$&amp;.&amp;&amp;</span></p>
  </section>

  <section class="menu-item col-right" style="top:200px;">
    <h2>Individual Quiche</h2>
    <p>Spinach &amp; Cheese, Local Tomato &amp; Applewood Smoked Bacon, Maple Sausage &amp; Redskin Potato, or Asparagus &amp; Crab.</p>
  </section>

  <section class="menu-item col-right" style="top:321px;">
    <h2>Farmhouse Breakfast</h2>
    <p>Country Cheddar Scrambled Eggs Served with Redskin Potato Hash Browns, Baked Spiced Apples, Fresh Baked Gourmet Muffins &amp; Buttery Biscuits, &amp;</p>
  </section>

  <section class="menu-item col-right" style="top:442px;">
    <p><em class="lead">Your Choice of One:</em> Applewood Smoked Bacon, Maple Sausage Links, or Country Ham.</p>
  </section>

  <div class="photo-band photo-plate" role="img" aria-label="Breakfast plate with toast, fried eggs, bacon, sausage and basil"></div>
  <div class="photo-band photo-wraps" role="img" aria-label="Two halves of a breakfast burrito wrap"></div>
  <div class="photo-band photo-quiche" role="img" aria-label="Slice of spinach quiche on a white plate"></div>
</main>
</body>
</html>
```